Design the Business card for NetVaultic

Business card required for a professional Cyber Security business.
Company Logo and Icon has already been provided however I would like other options for the logo and icon to compare to. Alternatively, please refine/enhance the image of the logo.icon I have already provided.

If you are going to use the provided logo and icon, I was thinking that the company raised Logo on White background would serve well on the front of the card. See attached. AND, a large company raised stand-alone icon to appear on black background on the back of the card with tagline 'Cyber Risk Management, Governance and Consulting' or 'Cyber Security for your Business' See attached.
Alternatively, provide your own design for the logo and icon.

Target Market(s)

Enterprise, Government, Financial.

Contact Information for Business Card

Tavin Orloweth
Founder and CEO

Email Address
Mobile Number
Website URL
LinkedIn URL

Logo Text

NetVaultic - see attached example of logo

Font styles to use
Other font styles liked:
• Berlin Sans FB

Requirements
Must have
• Clean large and bold icon on the back with tagline.
• Horizontal alignment,
Nice to have
• Round edges.
• Raised Logo/Icon
Should not have
• An unprofessional look and feel.

```html
<!DOCTYPE html>
<html lang="en">
<head>
<meta charset="utf-8">
<title>NetVaultic Business Card</title>
<link rel="stylesheet" href="https://fonts.googleapis.com/css2?family=Signika:wght@400;500&family=Roboto:wght@400&display=swap">
<style>
  :root {
    --stage: #e8e5e0;
    --card-front: #f6f6f6;
    --card-back: #1a1c1f;
    --brand-blue: #1f6fc0;
    --tag-blue: #4a6fc4;
    --accent-yellow: #f3b90f;
    --text-grey: #555a60;
    --divider: #c9c9c9;
  }
  * { margin: 0; padding: 0; box-sizing: border-box; }
  html, body { width: 1200px; height: 960px; overflow: hidden; }
  body { position: relative; background: var(--stage); }

  .card {
    position: absolute;
    width: 600px;
    height: 343px;
    box-shadow: 0 4px 10px rgba(0,0,0,0.35);
  }
  .card--front { left: 314px; top: 113px; background: var(--card-front); }
  .card--back  { left: 311px; top: 472px; background: var(--card-back); }

  .wordmark {
    position: absolute;
    font-family: "Signika", sans-serif;
    font-weight: 500;
    color: var(--brand-blue);
    display: flex;
    align-items: center;
    gap: 10px;
  }
  .wordmark__dot {
    border-radius: 50%;
    background: var(--brand-blue);
    flex: none;
  }
  .card--front .wordmark { left: 66px; top: 150px; font-size: 34px; }
  .card--front .wordmark__dot { width: 30px; height: 30px; }

  .divider {
    position: absolute;
    left: 326px; top: 102px;
    width: 1px; height: 140px;
    background: var(--divider);
  }

  .person { position: absolute; left: 354px; top: 104px; font-family: "Signika", sans-serif; }
  .person__name { font-size: 22px; font-weight: 500; color: var(--brand-blue); line-height: 1.1; }
  .person__title { font-size: 15px; color: var(--accent-yellow); margin-top: 1px; }

  .contacts { position: absolute; left: 354px; top: 160px; list-style: none; font-family: "Roboto", sans-serif; font-size: 14.5px; color: var(--text-grey); }
  .contacts li { display: flex; align-items: center; height: 19px; }
  .contacts svg { width: 14px; height: 14px; margin-right: 9px; flex: none; fill: var(--brand-blue); }

  .card--back .wordmark {
    left: 0; right: 0; top: 128px;
    justify-content: center;
    font-size: 46px;
    gap: 16px;
  }
  .card--back .wordmark__dot { width: 46px; height: 46px; }

  .tagline {
    position: absolute;
    left: 0; right: 0; top: 277px;
    text-align: center;
    font-family: "Signika", sans-serif;
    font-size: 18px;
    color: var(--tag-blue);
  }
  .tagline__accent { color: var(--accent-yellow); }
</style>
</head>
<body>

<section class="card card--front">
  <div class="wordmark"><span class="wordmark__dot"></span>NetVaultic</div>
  <div class="divider"></div>
  <div class="person">
    <div class="person__name">Tavin Orloweth</div>
    <div class="person__title">Founder &amp; CEO</div>
  </div>
  <ul class="contacts">
    <li>
      <svg viewBox="0 0 14 14"><rect x="3" y="0.5" width="8" height="13" rx="1.5"/><rect x="4.3" y="2" width="5.4" height="8.5" fill="#fff"/></svg>
      555 014 2738
    </li>
    <li>
      <svg viewBox="0 0 14 14"><rect x="0.5" y="3" width="13" height="9" rx="1"/><path d="M1 3.5 L7 8 L13 3.5" stroke="#fff" stroke-width="1.2" fill="none"/></svg>
      tavin@netvaultic.com
    </li>
    <li>
      <svg viewBox="0 0 14 14"><circle cx="7" cy="7" r="6.5"/><ellipse cx="7" cy="7" rx="2.6" ry="6" fill="none" stroke="#fff" stroke-width="1"/><line x1="1" y1="7" x2="13" y2="7" stroke="#fff" stroke-width="1"/></svg>
      www.netvaultic.com
    </li>
    <li>
      <svg viewBox="0 0 14 14"><circle cx="7" cy="7" r="6.5"/></svg>
      netvaultic
    </li>
  </ul>
</section>

<section class="card card--back">
  <div class="wordmark"><span class="wordmark__dot"></span>NetVaultic</div>
  <p class="tagline">Cyber Risk Management, <span class="tagline__accent">Governance &amp; Consulting</span></p>
</section>

</body>
</html>
```